​Silver Harbor Rhythm provides personal, friendly service in a fun and high energy environment. We are based in Vermont.

We would like a card that appeals to a wide range of audiences as we do a wide range of events. Please feel free to check out our website silverharborrhythm.net for inspiration.

Target Market(s)

weddings, corporate, birthday parties, colleges

Industry/Entity Type

Business

Contact Information for Business Card

Silver Harbor Rhythm
Providing Entertainment For All Occasions
555 274 9160
silverharborrhythm@mailnest.net
silverharborrhythm.net

```html
<!DOCTYPE html>
<html lang="en">
<head>
<meta charset="utf-8">
<title>Silver Harbor Rhythm — Business Card</title>
<link rel="stylesheet" href="https://fonts.googleapis.com/css2?family=Open+Sans:wght@400;600;700&display=swap">
<style>
  :root {
    --bg: #e9e6e1;
    --card-white: #ffffff;
    --brand-green: #2f5c12;
    --rule-dark: #1b1b1b;
    --divider: #d4d4d4;
    --text-dark: #333333;
    --text-light: #ffffff;
  }
  * { box-sizing: border-box; margin: 0; padding: 0; }
  html, body {
    width: 1200px; height: 829px; overflow: hidden;
    background: var(--bg);
    font-family: "Open Sans", sans-serif;
  }
  .stage {
    position: relative; width: 1200px; height: 829px;
    display: flex; align-items: center; justify-content: center; gap: 40px;
  }
  .card {
    position: relative; width: 540px; height: 309px; overflow: hidden;
    box-shadow: 0 6px 18px rgba(0,0,0,.18);
  }

  /* Front */
  .card-front { background: var(--card-white); }
  .front-brand {
    position: absolute; left: 30px; top: 92px; width: 220px;
    display: flex; align-items: center; gap: 8px;
  }
  .brand-square { width: 14px; height: 14px; background: var(--brand-green); flex: none; }
  .brand-name {
    color: var(--brand-green); font-weight: 700; font-size: 17px;
    line-height: 1.15; text-transform: uppercase; letter-spacing: .5px;
  }
  .front-divider {
    position: absolute; left: 262px; top: 0; width: 1px; height: 170px;
    background: var(--divider);
  }
  .contact { position: absolute; left: 278px; top: 34px; color: var(--text-dark); }
  .contact-name { color: var(--brand-green); font-weight: 700; font-size: 16px; line-height: 1.1; }
  .contact-title { font-weight: 600; font-size: 12px; margin: 2px 0 8px; }
  .contact-line {
    display: flex; align-items: center; gap: 6px;
    font-size: 11px; line-height: 18px;
  }
  .contact-line svg { width: 12px; height: 12px; flex: none; }
  .contact-address { font-size: 11px; line-height: 18px; margin-top: 6px; }
  .front-rule {
    position: absolute; left: 0; right: 0; top: 226px; height: 3px;
    background: var(--rule-dark);
  }
  .front-band {
    position: absolute; left: 0; right: 0; top: 233px; bottom: 0;
    background: var(--brand-green);
    display: flex; align-items: center; justify-content: center;
  }
  .web {
    color: var(--text-light); font-size: 16px; letter-spacing: 1px;
  }

  /* Back */
  .card-back { background: var(--brand-green); }
  .back-brand {
    position: absolute; left: 0; right: 0; top: 92px;
    display: flex; align-items: center; justify-content: center; gap: 14px;
  }
  .back-brand .brand-square { width: 26px; height: 26px; background: var(--text-light); }
  .back-brand .brand-name { color: var(--text-light); font-size: 34px; }
  .back-web {
    position: absolute; right: 40px; bottom: 40px;
    color: var(--text-light); font-size: 17px; letter-spacing: 1px;
  }
</style>
</head>
<body>
<main class="stage">
  <section class="card card-front" aria-label="Card front">
    <div class="front-brand">
      <span class="brand-square"></span>
      <span class="brand-name">Silver Harbor Rhythm</span>
    </div>
    <div class="front-divider"></div>
    <div class="contact">
      <p class="contact-name">Your Name</p>
      <p class="contact-title">Title</p>
      <p class="contact-line">
        <svg viewBox="0 0 12 12" aria-hidden="true"><circle cx="6" cy="6" r="6" fill="#2f5c12"/><path d="M4 3.2l1 1.4-.6.7c.4.8 1 1.4 1.8 1.8l.7-.6 1.4 1-.5 1c-2.3-.2-4.1-2-4.3-4.3z" fill="#fff"/></svg>
        555 274 9160
      </p>
      <p class="contact-line">
        <svg viewBox="0 0 12 12" aria-hidden="true"><circle cx="6" cy="6" r="6" fill="#2f5c12"/><rect x="3" y="4" width="6" height="4.2" fill="#fff"/><path d="M3 4l3 2.3L9 4" stroke="#2f5c12" stroke-width=".7" fill="none"/></svg>
        silverharborrhythm@mailnest.net
      </p>
      <p class="contact-address">Street Name, City Name<br>Zip Code-00000</p>
    </div>
    <div class="front-rule"></div>
    <div class="front-band"><span class="web">www.silverharborrhythm.net</span></div>
  </section>

  <section class="card card-back" aria-label="Card back">
    <div class="back-brand">
      <span class="brand-square"></span>
      <span class="brand-name">Silver Harbor Rhythm</span>
    </div>
    <span class="back-web">www.silverharborrhythm.net</span>
  </section>
</main>
</body>
</html>
```